New business card design

I need original, modern, business looking but dzen (minimalistic) looking design.
Also refer to websit travenko.ru

Text is

Веденин Олег, PMP
Партнер

Моб. +7 (915) 604 7189
info@travenko.ru
Москва, Россия, 119847, ул. Берёзовая 27/2
=====================

Vedenin Oleg, PMP
Partner

Mob. +7 (915) 604 7189
info@travenko.ru
Moscow, Russia,119847, Beryozovaya 27/2

```html
<!DOCTYPE html>
<html lang="ru">
<head>
<meta charset="utf-8">
<title>Travenko — business cards</title>
<link href="https://fonts.googleapis.com/css2?family=Roboto+Mono:wght@400;700&display=swap" rel="stylesheet">
<style>
  :root {
    --backdrop: #dcdcdc;
    --card: #ffffff;
    --ink: #111111;
    --accent: #1f7ec6;
    --brand: #2a8fd6;
    --rule: #1a1a1a;
  }
  html, body {
    margin: 0;
    padding: 0;
    width: 1200px;
    height: 503px;
    overflow: hidden;
    background: var(--backdrop);
  }
  .card {
    position: absolute;
    top: 118px;
    width: 459px;
    height: 265px;
    background: var(--card);
    font-family: "Roboto Mono", monospace;
    color: var(--ink);
  }
  .card--en { left: 79px; }
  .card--ru { left: 655px; }

  .brand {
    position: absolute;
    left: 28px;
    top: 104px;
    display: flex;
    align-items: center;
    gap: 12px;
  }
  .brand__mark {
    width: 40px;
    height: 40px;
    background: var(--brand);
  }
  .brand__name {
    font-size: 27px;
    font-weight: 400;
    color: var(--brand);
    letter-spacing: -0.5px;
  }

  .divider {
    position: absolute;
    left: 229px;
    top: 55px;
    width: 2px;
    height: 155px;
    background: var(--rule);
  }

  .details {
    position: absolute;
    left: 253px;
    top: 70px;
    white-space: nowrap;
  }
  .details__name {
    margin: 0;
    font-size: 14px;
    font-weight: 700;
    line-height: 16px;
  }
  .details__role {
    margin: 0 0 16px;
    font-size: 12px;
    font-weight: 700;
    line-height: 16px;
    color: var(--accent);
    letter-spacing: 0.5px;
  }
  .contact {
    display: flex;
    align-items: flex-start;
    gap: 7px;
    margin-bottom: 11px;
    font-size: 11px;
    line-height: 15px;
  }
  .contact__icon {
    flex: none;
    width: 14px;
    height: 14px;
    background: var(--accent);
    display: block;
  }
</style>
</head>
<body>

<section class="card card--en" lang="en">
  <div class="brand">
    <span class="brand__mark"></span>
    <span class="brand__name">Travenko</span>
  </div>
  <div class="divider"></div>
  <div class="details">
    <p class="details__name">VEDENIN OLEG, PMP</p>
    <p class="details__role">PARTNER</p>
    <div class="contact">
      <svg class="contact__icon" viewBox="0 0 14 14"><rect x="4.5" y="2.5" width="5" height="9" rx="1" fill="none" stroke="#fff" stroke-width="1.2"/></svg>
      <span>+7 (915) 604 7189</span>
    </div>
    <div class="contact">
      <svg class="contact__icon" viewBox="0 0 14 14"><circle cx="6" cy="6" r="3" fill="none" stroke="#fff" stroke-width="1.4"/><line x1="8.2" y1="8.2" x2="11" y2="11" stroke="#fff" stroke-width="1.6"/></svg>
      <span>info@travenko.ru</span>
    </div>
    <div class="contact">
      <svg class="contact__icon" viewBox="0 0 14 14"><path d="M7 12 C4.5 8.5 3.5 7 3.5 5.5 A3.5 3.5 0 0 1 10.5 5.5 C10.5 7 9.5 8.5 7 12 Z" fill="#fff"/><circle cx="7" cy="5.5" r="1.3" fill="#1f7ec6"/></svg>
      <span>Moscow, Russia<br>119847, Beryozovaya 27/2</span>
    </div>
  </div>
</section>

<section class="card card--ru" lang="ru">
  <div class="brand">
    <span class="brand__mark"></span>
    <span class="brand__name">Travenko</span>
  </div>
  <div class="divider"></div>
  <div class="details">
    <p class="details__name">ВЕДЕНИН ОЛЕГ, PMP</p>
    <p class="details__role">ПАРТНЕР</p>
    <div class="contact">
      <svg class="contact__icon" viewBox="0 0 14 14"><rect x="4.5" y="2.5" width="5" height="9" rx="1" fill="none" stroke="#fff" stroke-width="1.2"/></svg>
      <span>+7 (915) 604 7189</span>
    </div>
    <div class="contact">
      <svg class="contact__icon" viewBox="0 0 14 14"><circle cx="6" cy="6" r="3" fill="none" stroke="#fff" stroke-width="1.4"/><line x1="8.2" y1="8.2" x2="11" y2="11" stroke="#fff" stroke-width="1.6"/></svg>
      <span>info@travenko.ru</span>
    </div>
    <div class="contact">
      <svg class="contact__icon" viewBox="0 0 14 14"><path d="M7 12 C4.5 8.5 3.5 7 3.5 5.5 A3.5 3.5 0 0 1 10.5 5.5 C10.5 7 9.5 8.5 7 12 Z" fill="#fff"/><circle cx="7" cy="5.5" r="1.3" fill="#1f7ec6"/></svg>
      <span>Москва, Россия<br>119847, ул. Берёзовая 27/2</span>
    </div>
  </div>
</section>

</body>
</html>
```